Fresh, modern, fun business card for pediatric dental practice

Need a business card for fresh, modern, fun pediatric dental practice

Clean look that matches our website's font and colors

We prefer the look of curved corners on business cards

Target Market(s)

parents (mothers) of young children, professionals, mid-high class

Industry/Entity Type

Dental

Contact Information for Business Card

Maplebrook Pediatric Dentistry
482 Quarry Lane
Suite 517
Brookfield, PA 17599
717.555.0193
www.maplebrookkidsdental.example

Mei-Ran Tsai, DMD
Corinne Walbeck, DMD
(we are working on our email address, but we would like that on the card as well)

Font styles to use
Sans Serif

Requirements
Must have
• All info; we would also like to make cards for individual staff members
• colors from our website and color palatte, attatched
• use same font and design as website for branding
Nice to have
• clean, simple card that has a pop of color
• we would like to see a few designs with our tag line "where smiles get brighter"
• we are not sure if we want to have it on there or not
• we would like to see a few designs incorporating the ribbon graphic on our website where the word WELCOME is

```html
<!DOCTYPE html>
<html lang="en">
<head>
<meta charset="utf-8">
<title>Maplebrook Pediatric Dentistry – Business Card</title>
<link rel="stylesheet" href="https://fonts.googleapis.com/css2?family=Lato:wght@400;700&family=Roboto:wght@400;700&display=swap">
<style>
  :root {
    --magenta: #c92a8e;
    --sun: #f0b323;
    --white: #ffffff;
    --backdrop: #8f8f8f;
  }
  * { margin: 0; padding: 0; box-sizing: border-box; }
  html, body { width: 1200px; height: 1134px; overflow: hidden; }
  body {
    background: var(--backdrop);
    position: relative;
    font-family: "Lato", sans-serif;
  }
  .card {
    position: absolute;
    left: 261px;
    width: 675px;
    height: 381px;
    background: var(--magenta);
    border-radius: 15px;
    overflow: hidden;
  }
  .card--front { top: 161px; }
  .card--back { top: 589px; }

  .brand {
    position: absolute;
    text-align: center;
    color: var(--sun);
    font-family: "Lato", sans-serif;
    font-weight: 700;
    line-height: 1.15;
  }
  .brand__dot {
    display: block;
    margin: 0 auto 10px;
    border-radius: 50%;
    background: var(--sun);
  }
  .card--front .brand { left: 40px; width: 252px; top: 116px; font-size: 27px; }
  .card--front .brand__dot { width: 30px; height: 30px; }
  .card--back .brand { left: 0; width: 100%; top: 120px; font-size: 40px; }
  .card--back .brand__dot { width: 44px; height: 44px; margin-bottom: 14px; }

  .divider {
    position: absolute;
    left: 327px;
    top: 74px;
    width: 2px;
    height: 202px;
    background: var(--sun);
  }
  .details { position: absolute; left: 363px; top: 64px; }
  .doctors {
    font-family: "Roboto", sans-serif;
    font-weight: 700;
    font-size: 25px;
    line-height: 37px;
    color: var(--white);
  }
  .doctors .credential { color: var(--sun); font-weight: 400; }
  .address {
    margin-top: 14px;
    font-size: 16px;
    line-height: 22px;
    color: var(--white);
  }
  .contacts { list-style: none; margin-top: 14px; }
  .contacts li {
    display: flex;
    align-items: center;
    gap: 8px;
    font-size: 16px;
    line-height: 24px;
    color: var(--white);
  }
  .contacts svg { width: 19px; height: 19px; flex: none; }

  .ribbon {
    position: absolute;
    left: 0;
    top: 314px;
    width: 632px;
    height: 39px;
  }
  .ribbon svg { position: absolute; inset: 0; width: 100%; height: 100%; }
  .ribbon__label {
    position: absolute;
    left: 0;
    width: 654px;
    top: 0;
    line-height: 39px;
    text-align: center;
    font-family: "Roboto", sans-serif;
    font-size: 25px;
    color: var(--white);
  }
</style>
</head>
<body>

<section class="card card--front">
  <div class="brand">
    <span class="brand__dot"></span>
    maplebrook<br>pediatric dentistry
  </div>

  <div class="divider"></div>

  <div class="details">
    <p class="doctors">Mei-Ran Tsai, <span class="credential">DMD</span><br>Corinne Walbeck, <span class="credential">DMD</span></p>
    <p class="address">482 Quarry Lane, Suite 517<br>Brookfield, PA 17599</p>
    <ul class="contacts">
      <li>
        <svg viewBox="0 0 20 20" aria-hidden="true"><circle cx="10" cy="10" r="10" fill="#f0b323"/><path d="M7 5.5l1.8 2.6-1 1.1a7 7 0 0 0 3 3l1.1-1 2.6 1.8-1 1.6c-3.8.2-7.900-3.9-7.7-7.7z" fill="#c92a8e"/></svg>
        717.555.0193
      </li>
      <li>
        <svg viewBox="0 0 20 20" aria-hidden="true"><circle cx="10" cy="10" r="10" fill="#f0b323"/><rect x="5" y="6.5" width="10" height="7" rx="1" fill="#c92a8e"/><path d="M5.5 7l4.5 3.5L14.5 7" fill="none" stroke="#f0b323" stroke-width="1"/></svg>
        info@maplebrookkidsdental.example
      </li>
      <li>
        <svg viewBox="0 0 20 20" aria-hidden="true"><circle cx="10" cy="10" r="10" fill="#f0b323"/><circle cx="10" cy="10" r="5" fill="none" stroke="#c92a8e" stroke-width="1.4"/><path d="M5 10h10M10 5c-2.5 3-2.5 7 0 10M10 5c2.5 3 2.5 7 0 10" fill="none" stroke="#c92a8e" stroke-width="1"/></svg>
        www.maplebrookkidsdental.example
      </li>
    </ul>
  </div>

  <div class="ribbon">
    <svg viewBox="0 0 632 39" preserveAspectRatio="none" aria-hidden="true"><path d="M0 0H632L614 19.5L632 39H0z" fill="#f0b323"/></svg>
    <span class="ribbon__label">welcome</span>
  </div>
</section>

<section class="card card--back">
  <div class="brand">
    <span class="brand__dot"></span>
    maplebrook<br>pediatric dentistry
  </div>
</section>

</body>
</html>
```